Single-sided business card for restaurant velmora with new logo made on this site

Business card options with new logo including restaurant name, address, phone number and website. This business card is single-sided only and will be presented at the hostess desk for clients to take. I would like to see options based on a cream card background, a white card background, a yellow card background and a burgundy colored background. It needs to be elegant and traditional.

Target Market(s)

local and international crowd

Industry/Entity Type

restaurant

Contact Information for Business Card

address, website and phone number

Font styles to use
Serif

Colors
EE7325
F08F49
F5BC92
FAE3D3
FDF4ED

Requirements
Must have
• new logo, address, phone number, website
Should not have
• more than three colors

```html
<!DOCTYPE html>
<html lang="es">
<head>
<meta charset="utf-8">
<title>Velmora – Business Cards</title>
<link href="https://fonts.googleapis.com/css2?family=Cinzel:wght@400;600&family=Open+Sans:wght@400;600;700&display=swap" rel="stylesheet">
<style>
  :root {
    --backdrop: #7d7d7d;
    --burgundy: #3f1c1e;
    --gold: #f5b93a;
    --yellow: #f7c25b;
    --ink: #3f1c1e;
    --cream-text: #f4ece4;
  }
  * { box-sizing: border-box; margin: 0; padding: 0; }
  html, body { width: 1200px; height: 1002px; overflow: hidden; }
  body {
    background: var(--backdrop);
    font-family: "Open Sans", sans-serif;
    position: relative;
  }
  .card {
    position: absolute;
    top: 207px;
    width: 397px;
    height: 695px;
    text-align: center;
  }
  .card--burgundy { left: 144px; background: var(--burgundy); color: var(--cream-text); }
  .card--yellow { left: 650px; background: var(--yellow); color: var(--ink); }
  .card__frame {
    position: absolute;
    inset: 18px;
    border: 2px solid var(--gold);
  }
  .card--yellow .card__frame { border-color: var(--ink); }
  .brand-mark {
    position: absolute;
    left: 50%;
    width: 141px;
    height: 141px;
    transform: translateX(-50%);
  }
  .card--burgundy .brand-mark { top: 89px; background: var(--gold); }
  .card--yellow .brand-mark { top: 124px; background: var(--ink); }
  .brand-name {
    position: absolute;
    left: 0; right: 0;
    font-family: "Cinzel", serif;
    font-weight: 400;
    font-size: 44px;
    letter-spacing: 7px;
    padding-left: 7px;
    line-height: 1;
  }
  .card--burgundy .brand-name { top: 280px; color: #ffffff; }
  .card--yellow .brand-name { top: 315px; color: var(--ink); }
  .tagline {
    position: absolute;
    left: 0; right: 0;
    display: flex; justify-content: center; align-items: center; gap: 10px;
    font-family: "Cinzel", serif;
    font-size: 12px;
    font-weight: 600;
    letter-spacing: 0.5px;
    line-height: 14px;
  }
  .tagline__rule { width: 66px; height: 2px; background: var(--gold); }
  .card--burgundy .tagline { top: 336px; color: #ffffff; }
  .card--yellow .tagline { top: 371px; color: var(--ink); }
  .card--yellow .tagline__rule { background: var(--ink); }
  .contact { position: absolute; left: 0; right: 0; font-size: 17px; line-height: 26px; }
  .card--burgundy .contact { top: 407px; }
  .card--yellow .contact { top: 469px; }
  .contact__title { color: var(--gold); }
  .card--yellow .contact__title { color: var(--ink); font-weight: 600; }
  .divider {
    position: absolute;
    top: 542px; left: 0; right: 0;
    display: flex; justify-content: center; align-items: center; gap: 6px;
  }
  .divider__line { width: 64px; height: 2px; background: var(--gold); margin: 0 12px; }
  .divider svg { width: 22px; height: 22px; display: block; }
  .phone { position: absolute; left: 0; right: 0; }
  .card--burgundy .phone { top: 596px; font-size: 17px; line-height: 26px; }
  .card--yellow .phone { top: 576px; font-size: 28px; font-weight: 700; line-height: 36px; }
  .web { position: absolute; left: 0; right: 0; font-size: 17px; line-height: 26px; }
  .card--burgundy .web { top: 622px; }
  .card--yellow .web { top: 613px; }
</style>
</head>
<body>
  <section class="card card--burgundy">
    <div class="card__frame"></div>
    <div class="brand-mark"></div>
    <div class="brand-name">VELMORA</div>
    <div class="tagline"><span class="tagline__rule"></span><span>Desde 1999</span><span class="tagline__rule"></span></div>
    <div class="contact">
      <p class="contact__title">Restaurant Velmora</p>
      <p>Jacarandá 415</p>
      <p>Puerto Lirio, Oaxaca CP 70412</p>
    </div>
    <div class="divider">
      <span class="divider__line"></span>
      <svg viewBox="0 0 22 22" aria-label="Teléfono">
        <circle cx="11" cy="11" r="11" fill="#f5b93a"/>
        <path d="M7 6.5c.6-.6 1.4-.5 1.8.1l1 1.5c.3.5.2 1-.2 1.4l-.6.5c.6 1.3 1.6 2.3 2.9 2.9l.5-.6c.4-.4.9-.5 1.4-.2l1.5 1c.6.4.7 1.2.1 1.8l-.6.6c-.8.8-2.5.6-4.5-.9-1.5-1.1-2.7-2.4-3.6-3.9-1-1.7-1-3 .3-4.2z" fill="#3f1c1e"/>
      </svg>
      <svg viewBox="0 0 22 22" aria-label="Sitio web">
        <circle cx="11" cy="11" r="11" fill="#f5b93a"/>
        <g fill="none" stroke="#3f1c1e" stroke-width="1">
          <circle cx="11" cy="11" r="6"/>
          <ellipse cx="11" cy="11" rx="2.6" ry="6"/>
          <line x1="5" y1="11" x2="17" y2="11"/>
          <line x1="6" y1="8" x2="16" y2="8"/>
          <line x1="6" y1="14" x2="16" y2="14"/>
        </g>
      </svg>
      <span class="divider__line"></span>
    </div>
    <p class="phone">958-555-0142</p>
    <p class="web">www.velmora.com.mx</p>
  </section>

  <section class="card card--yellow">
    <div class="card__frame"></div>
    <div class="brand-mark"></div>
    <div class="brand-name">VELMORA</div>
    <div class="tagline"><span class="tagline__rule"></span><span>Desde 1999</span><span class="tagline__rule"></span></div>
    <div class="contact">
      <p class="contact__title">Restaurant Velmora</p>
      <p>Jacarandá 415</p>
      <p>Puerto Lirio, Oaxaca CP 70412</p>
    </div>
    <p class="phone">958-555-0142</p>
    <p class="web">www.velmora.com.mx</p>
  </section>
</body>
</html>
```